New design for www.TrimTable.com

On TrimTable you can find & book your hairdresser. TrimTable is the biggest platform in the Netherlands.

- The design should be a responcive design
- Should be able to go global, should fit in perfectly between all the big booking platforms like stayvo, ridlo etc,
- Should have te result of more bookings. :)
- We are ‘only’ asking a beautiful design, not a technical solution.
- We need a homepage (https://trimtable.com/), search resultpage ((https://trimtable.com/kapper/amsterdam/#), salonpage (https://trimtable.com/kapper/vorden/lumo-for-hair/), about us page (https://trimtable.com/aboutus/), for the hairdresser info page (https://trimtable.com/kapper/), login/register page (https://trimtable.com/account/signin/).

- On the page of the hairdresser there is a dynamic part. The part where you create your appointment. Please take a look at this part too after you choose your treatment (behandeling), employee (medewerker), Date (datum) and time (tijd). The part that you see after this, is the part where you fill in your data as a consumer.

I've added more logo's but mostly we use the green color.

A few of our competitors: www.plumsalo.com, www.korifex.com

Target Market(s)

All consumers

Industry/Entity Type

Hair And Beauty

Number of Pages Required

5+ page

Font styles to use
Sans Serif

Colors
abd036
c3c3c3
757575

Requirements
Must have
• Responsive
• We did an A/B test with the homepage. It turns out that option B works better then option A (take a look at the uploaded pictures). So what we need on the homepage: The USP's with the green checkboxes, The search button needs to by dynamic (changes for example from light green to dark green so you can see you can click it) The call to action sentence Zoek & Vind je kapsalon, the searchfield and searchbutton should be seperated.
Nice to have
• The style that we like is the flat design style. The website should be simple, clean and it should feel a bit like a luxury thing. Because an appointment with the hairdresser can be a real treat and luxury moment for yourself.
• The luxury feeling and flat design that is in the www.ridlo.com website is really nice for example. But then it has to be a bit more light and not so black and dark.

```html
<!DOCTYPE html>
<html lang="en">
<head>
<meta charset="utf-8">
<title>TrimTable – Find &amp; book your hairdresser</title>
<link rel="stylesheet" href="https://fonts.googleapis.com/css2?family=Raleway:wght@300;400;600;700&family=Open+Sans:wght@400;600&display=swap">
<style>
  :root {
    --green: #8cc63f;
    --green-dark: #76ad2c;
    --orange: #f47b20;
    --orange-dark: #e06a12;
    --ink: #3f3f3f;
    --grey: #757575;
    --grey-light: #c3c3c3;
    --footer-bg: #efefef;
    --bar-bg: #e2e2e2;
    --white: #ffffff;
  }
  * { box-sizing: border-box; margin: 0; padding: 0; }
  html, body { width: 1200px; height: 2264px; overflow: hidden; }
  body { font-family: "Open Sans", Arial, sans-serif; color: var(--ink); background: var(--white); position: relative; }
  .raleway { font-family: "Raleway", Arial, sans-serif; }

  /* Header */
  .site-header { height: 96px; display: flex; align-items: center; justify-content: space-between; padding: 0 190px 0 168px; }
  .brand { display: flex; align-items: center; gap: 10px; font-family: "Raleway", sans-serif; font-weight: 700; font-size: 30px; color: var(--green); }
  .brand-dot { width: 34px; height: 34px; border-radius: 50%; background: var(--green); }
  .auth { display: flex; gap: 14px; }
  .auth a { display: inline-block; width: 82px; height: 30px; line-height: 30px; text-align: center; color: var(--white); font-size: 12px; font-weight: 600; text-decoration: none; border-radius: 2px; }
  .auth .login { background: var(--orange); }
  .auth .signup { background: var(--green); }

  /* Hero */
  .hero { position: absolute; top: 96px; left: 0; width: 1200px; height: 504px; background: linear-gradient(110deg, #9a9591 0%, #6f6660 35%, #4b403a 55%, #8a847f 80%, #b8b4b0 100%); }
  .hero-content { position: absolute; inset: 0; text-align: center; color: var(--white); }
  .hero h1 { font-family: "Raleway", sans-serif; font-weight: 300; font-size: 38px; line-height: 50px; margin-top: 118px; text-shadow: 0 1px 3px rgba(0,0,0,.35); }
  .hero h1 .big { font-size: 46px; }
  .search { position: absolute; top: 262px; left: 330px; display: flex; gap: 8px; }
  .search input { width: 400px; height: 40px; border: 0; padding: 0 14px; font-size: 13px; color: var(--grey); font-family: inherit; }
  .search button { width: 118px; height: 40px; border: 0; background: var(--green); color: var(--white); font-size: 16px; font-family: "Raleway", sans-serif; font-weight: 600; }
  .dots { position: absolute; top: 458px; left: 564px; display: flex; gap: 8px; }
  .dots span { width: 12px; height: 12px; border-radius: 50%; background: rgba(255,255,255,.6); }
  .dots span.active { background: var(--white); }

  /* Stats */
  .stats { position: absolute; top: 600px; left: 0; width: 1200px; height: 300px; }
  .stat { position: absolute; top: 62px; width: 180px; text-align: center; }
  .stat-photo { width: 160px; height: 160px; border-radius: 50%; margin: 0 auto; display: flex; align-items: center; justify-content: center; background: radial-gradient(circle at 50% 40%, #8f847b, #4a413b); border: 3px solid #e8e8e8; }
  .stat-number { color: var(--white); font-family: "Raleway", sans-serif; font-size: 30px; font-weight: 400; text-shadow: 0 1px 3px rgba(0,0,0,.5); }
  .stat-label { margin-top: 14px; font-family: "Raleway", sans-serif; font-size: 16px; font-weight: 600; color: var(--ink); }

  /* App promo */
  .app-promo { position: absolute; top: 900px; left: 0; width: 1200px; height: 420px; background: var(--orange); color: var(--white); }
  .app-promo h2 { position: absolute; top: 92px; left: 184px; font-family: "Raleway", sans-serif; font-weight: 300; font-size: 34px; line-height: 42px; }
  .app-promo p { position: absolute; top: 188px; left: 184px; width: 470px; font-size: 12px; line-height: 19px; }
  .app-promo .download { position: absolute; top: 290px; left: 184px; width: 156px; height: 40px; line-height: 36px; text-align: center; border: 2px solid var(--white); border-radius: 6px; color: var(--white); text-decoration: none; font-size: 14px; font-family: "Raleway", sans-serif; font-weight: 600; }
  .phone-photo { position: absolute; top: 38px; left: 740px; width: 260px; height: 382px; background: linear-gradient(160deg, #f7f7f7 0%, #dcdcdc 45%, #e9b89a 70%, #d99a78 100%); border-radius: 26px 26px 0 0; }

  /* How it works */
  .how { position: absolute; top: 1320px; left: 0; width: 1200px; height: 400px; background: var(--white); }
  .how-tab { position: absolute; top: -2px; left: 470px; width: 260px; height: 48px; background: #f2f2f2; border-radius: 0 0 24px 24px; text-align: center; line-height: 48px; font-family: "Raleway", sans-serif; font-size: 18px; color: var(--ink); }
  .step { position: absolute; top: 88px; width: 260px; text-align: center; }
  .step svg { display: block; margin: 0 auto; }
  .step h3 { margin-top: 22px; font-family: "Raleway", sans-serif; font-size: 16px; font-weight: 600; color: var(--ink); }
  .step p { margin: 8px auto 0; width: 210px; font-size: 11px; line-height: 16px; color: var(--grey); }

  /* Subscribe */
  .subscribe { position: absolute; top: 1720px; left: 0; width: 1200px; height: 260px; background: linear-gradient(100deg, #55603f 0%, #3f4a2e 40%, #4d5838 70%, #6c7358 100%); text-align: center; color: var(--white); }
  .subscribe h2 { margin-top: 62px; font-family: "Raleway", sans-serif; font-weight: 400; font-size: 30px; }
  .subscribe p { margin-top: 8px; font-size: 15px; }
  .subscribe form { margin: 22px auto 0; display: flex; justify-content: center; gap: 0; }
  .subscribe input { width: 300px; height: 38px; border: 0; padding: 0 12px; font-family: inherit; font-size: 13px; color: var(--grey); }
  .subscribe button { width: 122px; height: 38px; border: 0; background: var(--green); color: var(--white); font-size: 15px; font-family: "Raleway", sans-serif; font-weight: 600; }

  /* Footer */
  .site-footer { position: absolute; top: 1980px; left: 0; width: 1200px; height: 230px; background: var(--footer-bg); }
  .footer-col { position: absolute; top: 44px; }
  .footer-col h4 { font-family: "Raleway", sans-serif; font-size: 15px; font-weight: 700; color: var(--ink); margin-bottom: 12px; }
  .footer-col li { list-style: none; font-size: 12px; line-height: 20px; color: var(--grey); }
  .footer-col .note { font-size: 12px; color: var(--grey); }
  .social { display: flex; gap: 10px; margin-top: 12px; }
  .social span { width: 18px; height: 18px; border-radius: 50%; background: var(--grey); }
  .bottom-bar { position: absolute; top: 2210px; left: 0; width: 1200px; height: 54px; background: var(--bar-bg); font-size: 11px; color: var(--grey); line-height: 54px; padding-left: 184px; }
</style>
</head>
<body>

<header class="site-header">
  <div class="brand"><span class="brand-dot"></span>TrimTable</div>
  <nav class="auth">
    <a class="login" href="#">LOG IN</a>
    <a class="signup" href="#">SIGN UP</a>
  </nav>
</header>

<section class="hero">
  <div class="hero-bg" role="img" aria-label="Photo of a barber trimming a client's beard in a salon" style="position:absolute;inset:0;"></div>
  <div class="hero-content">
    <h1>The greatest hairdresser bookings site in the<br><span class="big">Netherlands with 541 hairdressers</span></h1>
    <form class="search">
      <input type="text" placeholder="Enter up places or postcode">
      <button type="button">Search</button>
    </form>
    <div class="dots"><span class="active"></span><span></span><span></span><span></span></div>
  </div>
</section>

<section class="stats">
  <div class="stat" style="left:142px;">
    <div class="stat-photo" role="img" aria-label="Photo of a salon interior"><span class="stat-number">541</span></div>
    <div class="stat-label">Salons</div>
  </div>
  <div class="stat" style="left:327px;">
    <div class="stat-photo" role="img" aria-label="Photo of a hair treatment"><span class="stat-number">16,413</span></div>
    <div class="stat-label">Treatments for booking</div>
  </div>
  <div class="stat" style="left:510px;">
    <div class="stat-photo" role="img" aria-label="Photo of a client booking an appointment"><span class="stat-number">370,827</span></div>
    <div class="stat-label">Agreements</div>
  </div>
  <div class="stat" style="left:694px;">
    <div class="stat-photo" role="img" aria-label="Photo of a hairdresser at work"><span class="stat-number">7,160</span></div>
    <div class="stat-label">Hairdressers booking</div>
  </div>
  <div class="stat" style="left:878px;">
    <div class="stat-photo" role="img" aria-label="Photo of a happy salon client"><span class="stat-number">26,529</span></div>
    <div class="stat-label">Reliable reviews</div>
  </div>
</section>

<section class="app-promo">
  <h2>All the hairdressers of<br>Netherlands in your pocket?</h2>
  <p>Find a salon near you in seconds, check open times and real reviews, then book your next cut with a single tap. Our free app keeps all your appointments in one place and sends a reminder the day before, so you never miss a visit.</p>
  <a class="download" href="#">Download Now</a>
  <div class="phone-photo" role="img" aria-label="Photo of a hand holding a smartphone showing the booking app"></div>
</section>

<section class="how">
  <div class="how-tab">How It Works</div>

  <div class="step" style="left:190px;">
    <svg width="110" height="140" viewBox="0 0 110 140">
      <path d="M55 4 C26 4 6 25 6 52 C6 86 55 136 55 136 C55 136 104 86 104 52 C104 25 84 4 55 4 Z" fill="var(--green)"/>
      <circle cx="50" cy="48" r="18" fill="none" stroke="#fff" stroke-width="6"/>
      <line x1="63" y1="61" x2="76" y2="74" stroke="#fff" stroke-width="7" stroke-linecap="round"/>
    </svg>
    <h3>Search &amp; Find Hairdresser</h3>
    <p>Search by city or name and compare salons near you.</p>
  </div>

  <div class="step" style="left:470px;">
    <svg width="110" height="140" viewBox="0 0 110 140">
      <path d="M55 4 C26 4 6 25 6 52 C6 86 55 136 55 136 C55 136 104 86 104 52 C104 25 84 4 55 4 Z" fill="var(--green)"/>
      <rect x="31" y="30" width="48" height="44" rx="3" fill="none" stroke="#fff" stroke-width="4"/>
      <line x1="31" y1="42" x2="79" y2="42" stroke="#fff" stroke-width="4"/>
      <line x1="42" y1="24" x2="42" y2="34" stroke="#fff" stroke-width="4" stroke-linecap="round"/>
      <line x1="68" y1="24" x2="68" y2="34" stroke="#fff" stroke-width="4" stroke-linecap="round"/>
      <g fill="#fff"><rect x="38" y="49" width="7" height="6"/><rect x="51" y="49" width="7" height="6"/><rect x="64" y="49" width="7" height="6"/><rect x="38" y="61" width="7" height="6"/><rect x="51" y="61" width="7" height="6"/></g>
    </svg>
    <h3>Book your Appointment</h3>
    <p>Choose a treatment, a stylist and a time that suits you.</p>
  </div>

  <div class="step" style="left:750px;">
    <svg width="110" height="140" viewBox="0 0 110 140">
      <path d="M55 4 C26 4 6 25 6 52 C6 86 55 136 55 136 C55 136 104 86 104 52 C104 25 84 4 55 4 Z" fill="var(--green)"/>
      <circle cx="40" cy="66" r="9" fill="none" stroke="#fff" stroke-width="4"/>
      <circle cx="70" cy="66" r="9" fill="none" stroke="#fff" stroke-width="4"/>
      <line x1="46" y1="59" x2="72" y2="26" stroke="#fff" stroke-width="4" stroke-linecap="round"/>
      <line x1="64" y1="59" x2="38" y2="26" stroke="#fff" stroke-width="4" stroke-linecap="round"/>
    </svg>
    <h3>Enjoy your new hairstyle</h3>
    <p>Sit back, relax and walk out with a fresh new look.</p>
  </div>
</section>

<section class="subscribe">
  <div role="img" aria-label="Photo of a salon chair and styling station with green tint" style="position:absolute;inset:0;"></div>
  <div style="position:relative;">
    <h2>Nice TrimTable get tips? Subscribe!</h2>
    <p>Please keep in touch, get the best tips and salon offers first</p>
    <form>
      <input type="email" placeholder="Email address">
      <button type="button">Subscribe</button>
    </form>
  </div>
</section>

<footer class="site-footer">
  <div class="footer-col" style="left:184px;">
    <h4>Quick links</h4>
    <ul><li>About Us</li><li>How It Works</li><li>Blogs</li><li>Read Our Blog</li></ul>
  </div>
  <div class="footer-col" style="left:356px;">
    <h4>Sublinks</h4>
    <ul><li>Barber Amsterdam</li><li>Barber Eindhoven</li><li>Barber Tilburg</li></ul>
  </div>
  <div class="footer-col" style="left:516px;">
    <h4>Resources</h4>
    <ul><li>Barber Utrecht</li><li>Barber Nijmegen</li><li>Barber Arnhem</li></ul>
  </div>
  <div class="footer-col" style="left:672px;">
    <h4>Locations</h4>
    <ul><li>Barber Zwolle</li><li>Barber Haarlem</li><li>Barber Leiden</li></ul>
  </div>
  <div class="footer-col" style="left:836px;">
    <h4>Follow us</h4>
    <div class="note">Please connect with us on</div>
    <div class="social"><span></span><span></span><span></span><span></span></div>
  </div>
</footer>

<div class="bottom-bar">© 2024 TrimTable. All rights reserved. Terms of Use</div>

</body>
</html>
```